Business card for a new innovative and professional lawn care business

We need a business card design for a new lawn care business in Halifax NS Canada. We offer lawn services in Halifax & Bedford. Our services offered include lawn care, garden services, and property maintenance. We take pride in our work and are experienced at what we do. I would like to see a design that is double sided. On the backside I would like the something simple (maybe my logo preferably on blackround (linked below) with website link, Facebook page or something). The front I want to include contact info:
Morgan Pell
phone 902-555-0148
email - brookvaleyards.ca
facebook - Facebook.com/brookvaleyards
Instagram maybe ? - instagram.com/brookvaleyard
Serving Halifax and Bedford for 5 years?
I don't want it to have too much information as I will be passing them out in aim to visit website, or call !
We do want it to include lawn care, garden services and property maintenance.
Basic, catchy, and modern looking !
Logo attached below !

Target Market(s)

Passing business cards to everyone I meet or interact with.

Industry/Entity Type

Lawn Care

Contact Information for Business Card

Double sided with some basic information, with catchy colours and easy to look at.

Font styles to use
Sans Serif

Requirements
Must have
• Must be double sided and have :
• Name, Phone, Email, FB, Website, and 3 main services offered - lawn care, property maintenance, garden services
Nice to have
• Would be nice to have instagram link if it goes well on there
Should not have
• Don't want too much writing or images that are distracting

```html
<!DOCTYPE html>
<html lang="en">
<head>
<meta charset="utf-8">
<title>Brookvale Yards – Business Card</title>
<link href="https://fonts.googleapis.com/css2?family=Lato:wght@400;700;900&display=swap" rel="stylesheet">
<style>
  :root {
    --stage: #2b2b2b;
    --green: #7cc242;
    --green-deep: #2f8f2a;
    --ink: #2e2e2e;
    --ink-soft: #4a4a4a;
    --muted-light: #cfcfcf;
    --card-light-a: #ffffff;
    --card-light-b: #dcdcdc;
    --card-dark-a: #3a3a3a;
    --card-dark-b: #1c1c1c;
  }
  * { box-sizing: border-box; margin: 0; padding: 0; }
  html, body {
    width: 1200px; height: 873px; overflow: hidden;
    background: var(--stage);
    font-family: "Lato", Arial, sans-serif;
  }
  .stage { position: relative; width: 1200px; height: 873px; }
  .card {
    position: absolute; top: 282px;
    width: 540px; height: 309px; border-radius: 18px; overflow: hidden;
  }
  .card--back { left: 45px; }
  .card--front { left: 615px; }
  .card__texture { position: absolute; inset: 0; }
  .card--back .card__texture {
    background: linear-gradient(135deg, var(--card-dark-a) 0%, #272727 45%, var(--card-dark-b) 100%);
  }
  .card--front .card__texture {
    background: linear-gradient(135deg, var(--card-light-a) 0%, #eeeeee 50%, var(--card-light-b) 100%);
  }
  .brand {
    position: absolute; display: flex; align-items: center; gap: 10px;
    color: var(--green); font-weight: 900; white-space: nowrap;
  }
  .brand__dot { border-radius: 50%; background: var(--green); flex: none; }
  .card--back .brand { left: 50%; top: 46%; transform: translate(-50%, -50%); font-size: 40px; }
  .card--back .brand__dot { width: 30px; height: 30px; }
  .services {
    position: absolute; left: 0; right: 0; top: 188px; text-align: center;
    color: var(--muted-light); font-weight: 700; font-size: 13px; letter-spacing: 1.5px;
    text-transform: uppercase; white-space: nowrap;
  }
  .services__sep { color: var(--green); margin: 0 8px; }
  .card--front .brand { left: 190px; top: 40px; font-size: 26px; color: var(--green-deep); }
  .card--front .brand__dot { width: 20px; height: 20px; background: var(--green-deep); }
  .person { position: absolute; left: 85px; top: 180px; }
  .person__name { color: var(--green); font-weight: 900; font-size: 21px; letter-spacing: .5px; }
  .person__role { color: var(--ink); font-weight: 700; font-size: 14px; margin-top: 4px; margin-left: 14px; }
  .divider {
    position: absolute; left: 250px; top: 140px; width: 2px; height: 95px;
    background: linear-gradient(to bottom, rgba(124,194,66,0), var(--green) 55%, rgba(124,194,66,0));
  }
  .contacts { position: absolute; left: 272px; top: 112px; list-style: none; }
  .contacts li {
    display: flex; align-items: center; gap: 10px; height: 28px;
    color: var(--ink); font-weight: 700; font-size: 14px;
  }
  .contacts .icon {
    width: 20px; height: 20px; border-radius: 50%; background: var(--green);
    display: flex; align-items: center; justify-content: center; flex: none;
  }
  .website {
    position: absolute; left: 0; right: 0; bottom: 28px; text-align: center;
    color: var(--ink); font-weight: 900; font-size: 15px; letter-spacing: 7px;
  }
</style>
</head>
<body>
<main class="stage">
  <section class="card card--back" aria-label="Card back">
    <div class="card__texture" role="img" aria-label="Dark low-poly geometric background"></div>
    <div class="brand"><span class="brand__dot"></span>Brookvale Yards</div>
    <p class="services">Lawn Care<span class="services__sep">•</span>Garden Services<span class="services__sep">•</span>Property Maintenance</p>
  </section>

  <section class="card card--front" aria-label="Card front">
    <div class="card__texture" role="img" aria-label="Light grey low-poly geometric background"></div>
    <div class="brand"><span class="brand__dot"></span>Brookvale Yards</div>

    <div class="person">
      <p class="person__name">MORGAN PELL</p>
      <p class="person__role">Owner / Founder</p>
    </div>

    <div class="divider"></div>

    <ul class="contacts">
      <li><span class="icon">
        <svg width="11" height="11" viewBox="0 0 24 24"><path fill="#fff" d="M6.6 10.8a15 15 0 0 0 6.6 6.6l2.2-2.2c.3-.3.7-.4 1-.2 1.1.4 2.3.6 3.6.6.6 0 1 .4 1 1V20c0 .6-.4 1-1 1A17 17 0 0 1 3 4c0-.6.4-1 1-1h3.5c.6 0 1 .4 1 1 0 1.3.2 2.5.6 3.6.1.3 0 .7-.2 1z"/></svg>
      </span>902-555-0148</li>
      <li><span class="icon">
        <svg width="11" height="9" viewBox="0 0 22 16"><rect x="1" y="1" width="20" height="14" rx="1.5" fill="none" stroke="#fff" stroke-width="2"/><path d="M1 2l10 7 10-7" fill="none" stroke="#fff" stroke-width="2"/></svg>
      </span>contact@brookvaleyards.ca</li>
      <li><span class="icon"></span>/brookvaleyards</li>
      <li><span class="icon"></span>brookvaleyard</li>
    </ul>

    <p class="website">www.brookvaleyards.ca</p>
  </section>
</main>
</body>
</html>
```